Law Offices business card

Hi there, I'll need business card for the Law Offices of Colin Matheny. The information must convey his strategic approach and quick resolution to complex business litigation needs. Please emphasize Civil Litigation, Corporate Law, Business Governance and Real Estate Law. Colin has over 25 years of experience in these fields.The card should be modern and edgy and the message should be clear. Please consult his current website for ideas.

```html
<!DOCTYPE html>
<html lang="en">
<head>
<meta charset="utf-8">
<title>Law Offices of Colin Matheny – Business Card</title>
<link rel="stylesheet" href="https://fonts.googleapis.com/css2?family=Open+Sans:wght@400;600;700&display=swap">
<style>
  :root {
    --orange: #fa6400;
    --white: #ffffff;
    --ink: #3a3a3a;
    --rule-light: rgba(255,255,255,0.75);
    --rule-dark: #c9c9c9;
    --page: #ecebe8;
  }
  * { margin: 0; padding: 0; box-sizing: border-box; }
  html, body {
    width: 1200px; height: 900px; overflow: hidden;
    background: var(--page);
    font-family: "Open Sans", Arial, sans-serif;
  }
  .sheet {
    width: 1200px; height: 900px;
    display: flex; align-items: center; justify-content: center; gap: 40px;
  }
  .card {
    position: relative;
    width: 540px; height: 309px;
    box-shadow: 0 6px 18px rgba(0,0,0,0.18);
  }
  .card--front { background: var(--orange); color: var(--white); }
  .card--back { background: var(--white); color: var(--ink); }

  .services {
    position: absolute; top: 28px; left: 300px;
    list-style: none; font-size: 13px; font-weight: 600; line-height: 1.45;
  }
  .services li::before {
    content: ""; display: inline-block; width: 6px; height: 6px;
    border-radius: 50%; background: currentColor;
    margin: 0 10px 2px 0; vertical-align: middle;
  }
  .services__note {
    margin-top: 8px; padding-left: 16px;
    font-size: 12px; font-weight: 400; font-style: normal;
  }

  .brand {
    position: absolute; left: 34px; bottom: 40px;
    display: flex; align-items: center; gap: 14px;
  }
  .brand__dot { width: 58px; height: 58px; border-radius: 50%; }
  .brand__rule { width: 1px; height: 62px; }
  .card--front .brand__dot { background: var(--white); }
  .card--front .brand__rule { background: var(--rule-light); }
  .card--back .brand__dot { background: var(--orange); }
  .card--back .brand__rule { background: var(--rule-dark); }
  .brand__name {
    font-size: 19px; font-weight: 600; line-height: 1.15;
    text-transform: uppercase; letter-spacing: 0.5px;
  }
  .card--front .brand__name { color: var(--white); }
  .card--back .brand__name { color: var(--orange); }

  .contact {
    position: absolute; top: 26px; left: 330px;
    font-size: 11.5px; line-height: 1.5; color: var(--ink);
  }
  .contact__name { color: var(--orange); font-weight: 700; font-size: 15px; line-height: 1.3; }
  .contact__role { margin-bottom: 10px; }
  .contact__address { margin-bottom: 8px; }
  .contact__lines { list-style: none; padding-left: 26px; }
  .contact__lines li { display: flex; align-items: center; gap: 7px; }
  .contact__lines svg { width: 10px; height: 10px; fill: var(--orange); flex: none; }
</style>
</head>
<body>
<main class="sheet">
  <section class="card card--front" aria-label="Card front">
    <div class="services">
      <ul>
        <li>Civil Litigation</li>
        <li>Corporate Law</li>
        <li>Business Governance</li>
        <li>Real Estate Law</li>
      </ul>
      <p class="services__note">Over 25 years of experience</p>
    </div>
    <div class="brand">
      <span class="brand__dot"></span>
      <span class="brand__rule"></span>
      <p class="brand__name">Law Offices<br>of Colin Matheny</p>
    </div>
  </section>

  <section class="card card--back" aria-label="Card back">
    <div class="contact">
      <p class="contact__name">Colin Matheny</p>
      <p class="contact__role">Attorney</p>
      <p class="contact__address">118B Harbor Lane<br>Coral Bay, Florida 33412</p>
      <ul class="contact__lines">
        <li><svg viewBox="0 0 10 10"><path d="M2 0.5 L3.8 2.6 L2.8 3.8 Q4 6 6.2 7.2 L7.4 6.2 L9.5 8 L8.2 9.5 Q4 9 0.5 1.8 Z"/></svg>561-555-0142</li>
        <li><svg viewBox="0 0 10 10"><rect x="2.5" y="0.5" width="5" height="3"/><rect x="0.5" y="3.5" width="9" height="4.5" rx="1"/><rect x="2.5" y="7" width="5" height="2.5"/></svg>561-555-0187</li>
        <li><svg viewBox="0 0 10 10"><path d="M0.5 2 H9.5 V8.5 H0.5 Z M0.5 2 L5 5.5 L9.5 2" stroke="#fff" stroke-width="0.8"/></svg>colin@mathenylaw.com</li>
        <li><svg viewBox="0 0 10 10"><circle cx="5" cy="5" r="4.5"/></svg>www.mathenylaw.com</li>
      </ul>
    </div>
    <div class="brand">
      <span class="brand__dot"></span>
      <span class="brand__rule"></span>
      <p class="brand__name">Law Offices<br>of Colin Matheny</p>
    </div>
  </section>
</main>
</body>
</html>
```